Veldmark Supplies Business Card

Professional business card that stand out to our potential customers. Front and back with clean modern design

Industry/Entity Type

Oil and gas

Contact Information for Business Card

Name, address, website , office phone and cell number

Requirements
Must have
• Editable files for each employee

```html
<!DOCTYPE html>
<html lang="en">
<head>
<meta charset="utf-8">
<title>Veldmark Supplies – Business Card</title>
<link rel="stylesheet" href="https://fonts.googleapis.com/css2?family=Archivo:wght@400;800&family=Arimo:wght@400;700&display=swap">
<style>
  :root {
    --stage: #3d3d3d;
    --card-white: #ffffff;
    --brand-cyan: #06aed0;
    --brand-red: #ee1c25;
    --ink: #3a3a3a;
    --rule: #c9c9c9;
  }
  * { box-sizing: border-box; margin: 0; padding: 0; }
  html, body { width: 1200px; height: 803px; overflow: hidden; }
  body {
    background: var(--stage);
    font-family: "Arimo", Arial, sans-serif;
    position: relative;
  }
  .card {
    position: absolute;
    top: 253px;
    width: 520px;
    height: 297px;
    border-radius: 18px;
    overflow: hidden;
  }
  .card--front {
    left: 50px;
    background: var(--card-white);
    border-bottom: 5px solid var(--brand-cyan);
  }
  .card--back {
    left: 630px;
    background: var(--brand-cyan);
  }

  /* Front */
  .brand {
    position: absolute;
    top: 46px;
    right: 44px;
    display: flex;
    align-items: center;
    gap: 10px;
  }
  .brand__mark {
    width: 20px; height: 20px;
    background: var(--brand-red);
  }
  .brand__name {
    font-family: "Archivo", Arial, sans-serif;
    font-weight: 800;
    font-size: 22px;
    letter-spacing: 1px;
    text-transform: uppercase;
    color: var(--brand-red);
  }
  .brand-rule {
    position: absolute;
    top: 108px;
    right: 44px;
    width: 200px;
    border-top: 1px solid var(--rule);
  }
  .person {
    position: absolute;
    left: 34px;
    top: 176px;
  }
  .person__name {
    font-family: "Archivo", Arial, sans-serif;
    font-weight: 800;
    font-size: 24px;
    color: var(--brand-red);
    line-height: 1;
  }
  .person__title {
    font-size: 13px;
    color: var(--brand-cyan);
    margin-top: 3px;
  }
  .person__rule {
    width: 150px;
    border-top: 1px solid var(--rule);
    margin-top: 8px;
  }
  .contact {
    position: absolute;
    left: 34px;
    bottom: 20px;
    display: flex;
    align-items: stretch;
    gap: 12px;
    font-size: 12px;
    color: var(--ink);
    line-height: 1.45;
  }
  .contact__divider { border-left: 1px solid var(--ink); }
  .contact__line { display: flex; align-items: center; gap: 6px; }
  .contact__icon { width: 10px; height: 10px; flex: none; }

  /* Back */
  .back-brand {
    position: absolute;
    top: 118px;
    left: 0; right: 0;
    display: flex;
    justify-content: center;
    align-items: center;
    gap: 12px;
  }
  .back-brand__mark {
    width: 26px; height: 26px;
    background: var(--card-white);
  }
  .back-brand__name {
    font-family: "Archivo", Arial, sans-serif;
    font-weight: 800;
    font-size: 28px;
    letter-spacing: 1px;
    text-transform: uppercase;
    color: var(--card-white);
  }
  .back-web {
    position: absolute;
    bottom: 48px;
    left: 0; right: 0;
    text-align: center;
    font-size: 14px;
    color: var(--card-white);
  }
</style>
</head>
<body>
  <section class="card card--front" aria-label="Business card front">
    <div class="brand">
      <span class="brand__mark"></span>
      <span class="brand__name">Veldmark Supplies</span>
    </div>
    <div class="brand-rule"></div>

    <div class="person">
      <p class="person__name">Aldo Brennan</p>
      <p class="person__title">President</p>
      <div class="person__rule"></div>
    </div>

    <div class="contact">
      <div class="contact__address">
        <p>4120 Larkspur Road</p>
        <p>Halden, Canada 58213</p>
      </div>
      <div class="contact__divider"></div>
      <div class="contact__phones">
        <p class="contact__line">
          <svg class="contact__icon" viewBox="0 0 10 10"><path d="M2 0.5 L4 2.5 L3 3.8 Q4.5 6 6.2 7 L7.5 6 L9.5 8 L8 9.5 Q3.5 9 0.5 2 Z" fill="#ee1c25"/></svg>
          555-214-0831
        </p>
        <p class="contact__line">
          <svg class="contact__icon" viewBox="0 0 10 10"><rect x="2" y="0.5" width="6" height="9" rx="1" fill="none" stroke="#ee1c25" stroke-width="1.2"/></svg>
          555-382-1167
        </p>
      </div>
      <div class="contact__divider"></div>
      <div class="contact__online">
        <p class="contact__line">
          <svg class="contact__icon" viewBox="0 0 10 10"><rect x="0.5" y="2" width="9" height="6.5" fill="#ee1c25"/><path d="M0.5 2 L5 5.5 L9.5 2" fill="none" stroke="#fff" stroke-width="0.9"/></svg>
          info@veldmarksupplies.com
        </p>
        <p class="contact__line">
          <svg class="contact__icon" viewBox="0 0 10 10"><circle cx="5" cy="5" r="4.5" fill="#ee1c25"/><path d="M0.5 5 H9.5 M5 0.5 Q2 5 5 9.5 M5 0.5 Q8 5 5 9.5" fill="none" stroke="#fff" stroke-width="0.7"/></svg>
          www.veldmarksupplies.com
        </p>
      </div>
    </div>
  </section>

  <section class="card card--back" aria-label="Business card back">
    <div class="back-brand">
      <span class="back-brand__mark"></span>
      <span class="back-brand__name">Veldmark Supplies</span>
    </div>
    <p class="back-web">www.veldmarksupplies.com</p>
  </section>
</body>
</html>
```